Business Card for Professional Photographer

I'm looking for an eye catching modern clean design that compliments my logo/ website fonts & colours.
I specialise in architecture, corporate & commercial photography so I'm marketing to professional clients rather than portrait / wedding clients.

I would prefer to not have a solid black design.

My logo brand guide is as follows :

Main front font. : Reislust
Main font colour : #fff
Slogan front font : Ubuntu Bold
Monogram front font : Venti Medium
Container colour : #fff

I need print ready files in pdf .png & .eps formats.

Included in the files below are some screen grabs as reference to font & colours etc.

```html
<!DOCTYPE html>
<html lang="en">
<head>
<meta charset="utf-8">
<title>Clear Angle – Business Card</title>
<link href="https://fonts.googleapis.com/css2?family=Ubuntu:wght@300;400;700&family=Ubuntu+Condensed&family=Roboto:wght@400&display=swap" rel="stylesheet">
<style>
  :root {
    --backdrop: #3a3a3c;
    --card-black: #161618;
    --shade: rgba(12, 13, 18, 0.72);
    --tile-navy: #2a3a55;
    --tile-steel: #4a5568;
    --tile-warm: #6b5238;
    --tile-sand: #8a7458;
    --tile-sky: #3d5a7a;
    --tile-stone: #5c5a57;
    --gold-light: #f2d58c;
    --gold: #d9b25f;
    --gold-deep: #b98d3a;
    --ink: #141414;
    --white: #ffffff;
  }
  * { margin: 0; padding: 0; box-sizing: border-box; }
  html, body { width: 799px; height: 1200px; overflow: hidden; }
  body {
    background: var(--backdrop);
    font-family: "Ubuntu", sans-serif;
    position: relative;
  }
  .card {
    position: absolute;
    left: 50px;
    width: 700px;
    height: 400px;
    border-radius: 4px;
    overflow: hidden;
    box-shadow: 0 10px 30px rgba(0,0,0,.45);
  }
  .card--front { top: 110px; }
  .card--back { top: 690px; background: var(--card-black); }

  /* Front: photo collage */
  .front__collage {
    position: absolute; inset: 0;
    display: grid;
    grid-template-columns: 30% 27% 43%;
    grid-template-rows: 38% 34% 28%;
    gap: 4px;
    background: #0d0e12;
  }
  .tile { width: 100%; height: 100%; }
  .tile--a { grid-column: 1; grid-row: 1 / 3; background: linear-gradient(160deg, var(--tile-warm), var(--tile-navy)); }
  .tile--b { grid-column: 2; grid-row: 1; background: linear-gradient(180deg, var(--tile-sand), var(--tile-stone)); }
  .tile--c { grid-column: 3; grid-row: 1 / 3; background: linear-gradient(135deg, var(--tile-sky), var(--tile-steel) 60%, var(--tile-navy)); }
  .tile--d { grid-column: 2; grid-row: 2 / 4; background: linear-gradient(200deg, var(--tile-warm), var(--tile-stone)); }
  .tile--e { grid-column: 1; grid-row: 3; background: linear-gradient(120deg, var(--tile-navy), var(--tile-steel)); }
  .tile--f { grid-column: 3; grid-row: 3; background: linear-gradient(90deg, var(--tile-stone), var(--tile-sand)); }
  .front__shade { position: absolute; inset: 0; background: var(--shade); }

  .front__brand {
    position: absolute;
    left: 90px; top: 110px;
    display: flex; align-items: center; gap: 26px;
  }
  .front__mark {
    width: 100px; height: 100px;
    border: 6px solid var(--gold);
    border-radius: 50%;
    flex: none;
  }
  .brand-name {
    font-family: "Ubuntu", sans-serif;
    font-weight: 300;
    color: var(--gold);
    letter-spacing: 0.16em;
    text-transform: uppercase;
    white-space: nowrap;
  }
  .front__name { font-size: 38px; }
  .tagline {
    font-family: "Ubuntu", sans-serif;
    font-weight: 700;
    letter-spacing: 0.2em;
    white-space: nowrap;
  }
  .front__tagline { font-size: 12px; color: var(--gold); margin-top: 2px; }
  .front__web {
    position: absolute; left: 90px; top: 270px;
    font-size: 19px; color: var(--gold);
    letter-spacing: 0.2em; font-weight: 400;
  }

  /* Back */
  .back__head { position: absolute; left: 40px; top: 32px; }
  .back__name { font-size: 36px; }
  .back__tagline { font-size: 12px; color: var(--white); margin-top: 6px; }
  .back__band {
    position: absolute; left: 0; top: 125px;
    width: 430px; height: 190px;
    background: linear-gradient(135deg, var(--gold-deep), var(--gold-light) 60%, var(--gold));
    padding: 16px 0 0 40px;
    color: var(--ink);
  }
  .person__name { font-family: "Ubuntu Condensed", sans-serif; font-size: 26px; font-weight: 700; line-height: 1.1; }
  .person__role { font-size: 15px; margin-bottom: 12px; }
  .contact { list-style: none; font-family: "Roboto", sans-serif; font-size: 16px; }
  .contact li { display: flex; align-items: center; gap: 12px; height: 24px; }
  .contact svg { width: 14px; height: 14px; fill: var(--ink); flex: none; }
  .back__mark {
    position: absolute; left: 410px; top: 150px;
    width: 215px; height: 215px;
    border: 8px solid var(--gold);
    border-radius: 26px;
    background: var(--card-black);
  }
  .back__strip {
    position: absolute; right: 0; top: 220px;
    width: 36px; height: 180px;
    background: linear-gradient(180deg, var(--gold-light), var(--gold));
  }
  .back__address {
    position: absolute; left: 40px; top: 340px;
    font-family: "Roboto", sans-serif; font-size: 16px; color: var(--white);
  }
</style>
</head>
<body>
  <section class="card card--front">
    <div class="front__collage">
      <div class="tile tile--a" role="img" aria-label="Architectural interior photograph"></div>
      <div class="tile tile--b" role="img" aria-label="Commercial product photograph"></div>
      <div class="tile tile--c" role="img" aria-label="Modern building exterior against sky"></div>
      <div class="tile tile--d" role="img" aria-label="Corporate workspace photograph"></div>
      <div class="tile tile--e" role="img" aria-label="Waterfront architecture photograph"></div>
      <div class="tile tile--f" role="img" aria-label="Interior detail photograph"></div>
    </div>
    <div class="front__shade"></div>
    <div class="front__brand">
      <div class="front__mark"></div>
      <div>
        <div class="brand-name front__name">Clear Angle</div>
        <div class="tagline front__tagline">Architecture Corporate Commercial</div>
      </div>
    </div>
    <div class="front__web">www.clearangle.com.au</div>
  </section>

  <section class="card card--back">
    <header class="back__head">
      <div class="brand-name back__name">Clear Angle</div>
      <div class="tagline back__tagline">Architecture Corporate Commercial</div>
    </header>
    <div class="back__band">
      <div class="person__name">Owen Harper</div>
      <div class="person__role">Photographer</div>
      <ul class="contact">
        <li><svg viewBox="0 0 24 24"><path d="M6.6 10.8a15 15 0 0 0 6.6 6.6l2.2-2.2a1 1 0 0 1 1-.25 11.4 11.4 0 0 0 3.6.57 1 1 0 0 1 1 1V20a1 1 0 0 1-1 1A17 17 0 0 1 3 4a1 1 0 0 1 1-1h3.5a1 1 0 0 1 1 1c0 1.25.2 2.45.57 3.57a1 1 0 0 1-.25 1z"/></svg>0412587306</li>
        <li><svg viewBox="0 0 24 24"><path d="M2 5h20v14H2z M3 6l9 7 9-7" stroke="#f2d58c" stroke-width="1.5"/></svg>info@clearangle.com.au</li>
        <li><svg viewBox="0 0 24 24"><circle cx="12" cy="12" r="10"/><path d="M2 12h20M12 2c3 3 3 17 0 20M12 2c-3 3-3 17 0 20" stroke="#f2d58c" stroke-width="1.5" fill="none"/></svg>www.clearangle.com.au</li>
      </ul>
    </div>
    <div class="back__mark"></div>
    <div class="back__strip"></div>
    <div class="back__address">48 Elm Rd Ballarat Vic 3350</div>
  </section>
</body>
</html>
```